Private Dining Restaurant Menu Design

Looking for help in designing a private dining room menu brochure - probably would need 4 panel layout to make all of the content fit, or a 5.5x8" booklet. Open to your ideas on layout/vessel - would want to post on website and be able to print to hand out to guests interested in booking our private dining room.

All content is in the attached "Private Dining Menu".

Would like to match existing dinner menu design - also attached.

Website is www.copperkettlebistro.com

Requirements
Must have
• Easy to read format of a brochure of the private dining menu content - want to be able to hand out to interested guests and have it simple and easy to read/flip through.

```html
<!DOCTYPE html>
<html lang="en">
<head>
<meta charset="utf-8">
<title>Private Dining Menu – Copper Kettle Bistro</title>
<link rel="stylesheet" href="https://fonts.googleapis.com/css2?family=Josefin+Sans:ital,wght@0,600;0,700;1,600&family=Barlow+Semi+Condensed:wght@500;600&family=Barlow:wght@400;500&display=swap">
<style>
  :root{
    --brick:#8a2b24;
    --navy:#1a2a56;
    --ink:#1c1c1c;
    --cream:#ece8da;
    --page-gray:#eceef1;
    --wood:#e9e6d8;
    --white:#ffffff;
  }
  *{margin:0;padding:0;box-sizing:border-box}
  html,body{width:1200px;height:900px;overflow:hidden;background:var(--white)}
  body{position:relative;font-family:"Barlow",Arial,sans-serif;color:var(--ink)}
  .spread{position:absolute;left:52px;top:52px;width:1098px;height:798px;box-shadow:0 0 6px rgba(0,0,0,.18);background:var(--white);overflow:hidden}
  .page{position:absolute;top:0;height:100%}
  .page-left{left:0;width:548px;background:var(--white)}
  .page-right{left:548px;width:550px;background:var(--page-gray)}
  .wood-texture{position:absolute;left:0;top:180px;width:260px;height:618px;background:radial-gradient(ellipse at 30% 50%,var(--wood) 0%,rgba(233,230,216,.5) 45%,rgba(255,255,255,0) 75%)}
  .kitchen-doodles{position:absolute;inset:0;background:linear-gradient(180deg,#eef0f3,#e6e9ed)}

  .section-title{display:flex;align-items:center;gap:8px;font-family:"Josefin Sans",sans-serif;font-weight:700;letter-spacing:1px;text-transform:uppercase}
  .section-title::before,.section-title::after{content:"";flex:1;height:2px;background:currentColor}

  .dinner{position:absolute;left:50px;top:46px;width:450px;text-align:center}
  .dinner .section-title{color:var(--brick);font-size:27px}
  .lead{font-family:"Josefin Sans",sans-serif;font-style:italic;font-weight:600;font-size:15px;line-height:20px;margin-top:6px}
  .note{font-size:12.5px;line-height:15px;margin-top:6px}
  .option{margin-top:20px}
  .option-name{font-family:"Barlow Semi Condensed",sans-serif;font-weight:600;font-size:22px;line-height:24px}
  .option-name .price{font-family:"Josefin Sans",sans-serif;font-style:italic;font-size:16px}
  .option-desc{font-size:12.5px;line-height:15px;margin-top:3px}
  .entrees{list-style:none;margin-top:7px;font-family:"Barlow Semi Condensed",sans-serif;font-weight:600;font-size:18.5px;line-height:23.5px;text-transform:uppercase}

  .dessert{position:absolute;left:50px;top:536px;width:450px;height:211px;background:var(--cream);border:1.5px solid var(--brick);text-align:center;padding:18px 20px 0}
  .dessert .section-title{color:var(--brick);font-size:26px}
  .dessert-list{list-style:none;margin-top:12px}
  .dessert-item{margin-bottom:9px}
  .dessert-name{font-family:"Barlow Semi Condensed",sans-serif;font-weight:600;font-size:17.5px;line-height:20px;text-transform:uppercase}
  .dessert-name .price{font-family:"Josefin Sans",sans-serif;font-style:italic;font-size:14px;text-transform:none}
  .dessert-name small{font-size:11px}
  .dessert-sub{font-family:"Barlow Semi Condensed",sans-serif;font-weight:600;font-size:11.5px;line-height:13px}

  .beverages{position:absolute;left:51px;top:0;width:449px;height:505px;background:var(--navy);color:var(--white);text-align:center;padding:46px 40px 0}
  .beverages .section-title{font-size:27px}
  .beverages .lead{font-size:15px;line-height:19px;margin-top:8px}
  .host-list{list-style:none;margin-top:20px}
  .host{margin-bottom:14px}
  .host-name{font-family:"Barlow Semi Condensed",sans-serif;font-weight:600;font-size:19px;line-height:22px;text-transform:uppercase}
  .host-name .price{font-family:"Josefin Sans",sans-serif;font-style:italic;font-size:15px}
  .host-desc{font-size:12.5px;line-height:15.5px;margin-top:2px}

  .room-photo{position:absolute;top:538px;height:213px;background:linear-gradient(180deg,#8a7a62 0%,#5a4a3a 35%,#e8e2d6 70%,#5a5048 100%)}
  .room-photo.wide{left:47px;width:250px}
  .room-photo.narrow{left:305px;width:198px}
</style>
</head>
<body>
  <div class="spread">
    <section class="page page-left">
      <div class="wood-texture" role="img" aria-label="Faint wood grain texture"></div>

      <div class="dinner">
        <h2 class="section-title">Dinner Options</h2>
        <p class="lead">An option below must be chosen for groups of 15 or more,<br>served after 3pm</p>
        <p class="note">It is greatly appreciated if you are able to give predetermined individual<br>menu orders to help with food prep and operations of the event</p>

        <div class="option">
          <h3 class="option-name">OPTION A <span class="price">- $20/Person</span></h3>
          <p class="option-desc">Served with bacon &amp; scallion mashed potatoes and steamed broccoli,<br>and choice of starter house or Caesar salad.</p>
          <ul class="entrees">
            <li>½ Copper Kettle's Famous Wood-Roasted Chicken</li>
            <li>½ Slab Sweet &amp; Smoky BBQ Baby Back Ribs</li>
            <li>6 oz Fresh Norwegian Salmon</li>
            <li>6 oz Wood-Grilled Sirloin</li>
          </ul>
        </div>

        <div class="option">
          <h3 class="option-name">OPTION B <span class="price">- $27/Person</span></h3>
          <p class="option-desc">Served with bacon &amp; scallion mashed potatoes and steamed broccoli,<br>and choice of starter house or Caesar salad.</p>
          <ul class="entrees">
            <li>30-Day Aged Wood-Grilled Ribeye – 14 oz</li>
            <li>6 oz Wood-Grilled Sirloin &amp; Grilled Shrimp</li>
            <li>½ Slab BBQ Ribs &amp; ¼ Wood-Roasted Chicken</li>
            <li>Full Rack of BBQ Baby Back Ribs</li>
          </ul>
        </div>
      </div>

      <div class="dessert">
        <h2 class="section-title">Desert Options</h2>
        <ul class="dessert-list">
          <li class="dessert-item">
            <p class="dessert-name">House Made Cheesecake Slice <span class="price">- $5/slice</span></p>
            <p class="dessert-sub">TURTLE, STRAWBERRY, OR PLAIN</p>
          </li>
          <li class="dessert-item">
            <p class="dessert-name">Whole House Made Cheesecake <span class="price">- $60 <small>(15 slices at $4/slice)</small></span></p>
            <p class="dessert-sub">TURTLE, STRAWBERRY, OR PLAIN</p>
          </li>
          <li class="dessert-item">
            <p class="dessert-name">Assorted Bars &amp; Cookie Platter <span class="price">- $25</span></p>
            <p class="dessert-sub">25 BARS/COOKIES</p>
          </li>
        </ul>
      </div>
    </section>

    <section class="page page-right">
      <div class="kitchen-doodles" role="img" aria-label="Faint sketched kitchen utensils and food background"></div>

      <div class="beverages">
        <h2 class="section-title">Beverages</h2>
        <p class="lead">We offer a full bar with a variety of non-alcoholic<br>beverages, liquor, beer, and wine options.<br>All beverages will be charged at menu prices.</p>
        <ul class="host-list">
          <li class="host">
            <h3 class="host-name">NA Beverage Host</h3>
            <p class="host-desc">Soda, Iced Tea, Lemonade, Coffee, and Hot Tea hosted<br>by renter for their guests.</p>
          </li>
          <li class="host">
            <h3 class="host-name">Full Host</h3>
            <p class="host-desc">All NA and Alcoholic beverages to be hosted by<br>the renter for their guests.</p>
          </li>
          <li class="host">
            <h3 class="host-name">Partial Host</h3>
            <p class="host-desc">A set amount or certain types of beverages hosted by the<br>renter for their guests.</p>
          </li>
          <li class="host">
            <h3 class="host-name">Cash Bar</h3>
            <p class="host-desc">Each beverage will be paid for by each individual guest.</p>
          </li>
          <li class="host">
            <h3 class="host-name">Corkage <span class="price">- $12</span></h3>
            <p class="host-desc">Per bottle of wine brought in.</p>
          </li>
        </ul>
      </div>

      <div class="room-photo wide" role="img" aria-label="Photo of the private dining room with set tables and a stone fireplace"></div>
      <div class="room-photo narrow" role="img" aria-label="Photo of the private dining room from another angle with pendant lights"></div>
    </section>
  </div>
</body>
</html>
```